German Headhunter/ HR Consultancy needs Business Cards Design

We need a business Card Design for our Company in Stuttgart. We are specialized as Headhunter/ HR Consultancy in Placement of specialist and managers in permanent employment. Please refer to our business logo.

```html
<!DOCTYPE html>
<html lang="de">
<head>
<meta charset="utf-8">
<title>Kernwerk Personalberatung – Visitenkarte</title>
<link href="https://fonts.googleapis.com/css2?family=Arimo:wght@400;700&family=Montserrat:wght@700&display=swap" rel="stylesheet">
<style>
  :root {
    --brand-blue: #3b55a8;
    --ink: #222222;
    --muted-grey: #9a9a9a;
    --paper: #ffffff;
    --backdrop: #e6e7e9;
  }
  * { margin: 0; padding: 0; box-sizing: border-box; }
  html, body { width: 1200px; height: 900px; overflow: hidden; }
  body {
    background: var(--backdrop);
    font-family: "Arimo", Arial, sans-serif;
    display: flex;
    flex-direction: column;
    align-items: center;
    justify-content: center;
    gap: 44px;
  }
  .card {
    width: 630px;
    height: 360px;
    position: relative;
    overflow: hidden;
    box-shadow: 0 6px 18px rgba(0,0,0,0.12);
  }

  /* Front side */
  .card--front {
    background: var(--brand-blue);
    display: flex;
    align-items: center;
    justify-content: center;
  }
  .brand {
    display: flex;
    align-items: center;
    gap: 18px;
  }
  .brand__square {
    width: 34px;
    height: 34px;
    background: var(--paper);
  }
  .brand__name {
    font-family: "Montserrat", sans-serif;
    font-weight: 700;
    color: var(--paper);
    line-height: 1.05;
    text-transform: uppercase;
  }
  .brand__name .line-main { display: block; font-size: 44px; letter-spacing: 1px; }
  .brand__name .line-sub { display: block; font-size: 19px; letter-spacing: 2.5px; }

  /* Back side */
  .card--back { background: var(--paper); }
  .back__brand {
    position: absolute;
    left: 44px;
    top: 40px;
    display: flex;
    align-items: center;
    gap: 12px;
  }
  .back__brand .brand__square { width: 22px; height: 22px; background: var(--brand-blue); }
  .back__brand .brand__name { color: var(--brand-blue); }
  .back__brand .line-main { font-size: 28px; }
  .back__brand .line-sub { font-size: 12px; letter-spacing: 1.6px; }

  .accent-bar {
    position: absolute;
    left: 0;
    top: 132px;
    width: 30px;
    height: 30px;
    background: var(--brand-blue);
  }
  .person {
    position: absolute;
    left: 44px;
    top: 128px;
  }
  .person__name {
    font-weight: 700;
    font-size: 26px;
    color: var(--brand-blue);
    letter-spacing: 0.5px;
  }
  .person__role { font-size: 15px; color: var(--ink); margin-top: 2px; }
  .address {
    position: absolute;
    left: 44px;
    top: 200px;
    font-size: 15px;
    color: var(--ink);
    line-height: 1.3;
  }
  .contacts {
    position: absolute;
    left: 44px;
    top: 252px;
    list-style: none;
    font-size: 15px;
    color: var(--ink);
  }
  .contacts li { display: flex; align-items: center; gap: 8px; line-height: 1.45; }
  .contacts svg { width: 13px; height: 13px; fill: var(--brand-blue); flex: none; }

  .band-blue {
    position: absolute;
    left: 0;
    right: 0;
    bottom: 0;
    height: 12px;
    background: var(--brand-blue);
  }
  .band-grey {
    position: absolute;
    right: 0;
    top: 0;
    bottom: 12px;
    width: 10px;
    background: var(--muted-grey);
  }
</style>
</head>
<body>

  <section class="card card--front" aria-label="Vorderseite">
    <div class="brand">
      <span class="brand__square"></span>
      <p class="brand__name">
        <span class="line-main">Kernwerk</span>
        <span class="line-sub">Personalberatung</span>
      </p>
    </div>
  </section>

  <section class="card card--back" aria-label="Rückseite">
    <div class="back__brand">
      <span class="brand__square"></span>
      <p class="brand__name">
        <span class="line-main">Kernwerk</span>
        <span class="line-sub">Personalberatung</span>
      </p>
    </div>

    <span class="accent-bar"></span>
    <div class="person">
      <p class="person__name">LENA HARTMANN</p>
      <p class="person__role">CEO/Founder</p>
    </div>

    <p class="address">52 Lindenweg<br>Suite 4 Stuttgart, 70173</p>

    <ul class="contacts">
      <li>
        <svg viewBox="0 0 24 24" aria-hidden="true"><path d="M6.6 10.8a15.1 15.1 0 0 0 6.6 6.6l2.2-2.2a1 1 0 0 1 1-.25 11.4 11.4 0 0 0 3.6.57 1 1 0 0 1 1 1V20a1 1 0 0 1-1 1A17 17 0 0 1 3 4a1 1 0 0 1 1-1h3.5a1 1 0 0 1 1 1c0 1.25.2 2.45.57 3.57a1 1 0 0 1-.25 1z"/></svg>
        (0711) 555 - 0182
      </li>
      <li>
        <svg viewBox="0 0 24 24" aria-hidden="true"><path d="M2 5h20v14H2z M4 7v.5l8 5 8-5V7l-8 5z" fill-rule="evenodd"/></svg>
        info@kernwerkpersonal.com
      </li>
      <li>
        <svg viewBox="0 0 24 24" aria-hidden="true"><path d="M12 2a10 10 0 1 0 0 20 10 10 0 0 0 0-20zm6.9 6h-3a15.6 15.6 0 0 0-1.4-3.6A8 8 0 0 1 18.9 8zM12 4a13.9 13.9 0 0 1 1.9 4h-3.8A13.9 13.9 0 0 1 12 4zM4.3 14a8 8 0 0 1 0-4h3.4a16.5 16.5 0 0 0 0 4zm.8 2h3a15.6 15.6 0 0 0 1.4 3.6A8 8 0 0 1 5.1 16zM8 8H5.1a8 8 0 0 1 4.3-3.6A15.6 15.6 0 0 0 8 8zm4 12a13.9 13.9 0 0 1-1.9-4h3.8A13.9 13.9 0 0 1 12 20zm2.3-6H9.7a14.7 14.7 0 0 1 0-4h4.6a14.7 14.7 0 0 1 0 4zm.3 5.6A15.6 15.6 0 0 0 16 16h3a8 8 0 0 1-4.4 3.6zM16.3 14a16.5 16.5 0 0 0 0-4h3.4a8 8 0 0 1 0 4z"/></svg>
        www.kernwerkpersonal.com
      </li>
    </ul>

    <span class="band-grey"></span>
    <span class="band-blue"></span>
  </section>

</body>
</html>
```